Boutique custom software development company needs new business card

Our nearly 20 year old custom software development company would like to better include the fact that we are now providing Bitcoin services. These new services are B2B include education (how to acquire and securely hold Bitcoin) and integrating Bitcoin payments into existing ecommerce sites or other existing systems. Please keep the card clean and simple. Attached is our current design and some other files. vextorial.com

Target Market(s)

businesses owners interested in long term relationship

Industry/Entity Type

Custom software development and Bitcoin

Contact Information for Business Card

Dale Parker, dale@vextorial.com, vextorial.com, (888) 555-VXTRL

Font styles to use
Other font styles liked:
• monospace

Requirements
Must have
• double-sided
Nice to have
• clean and simple
Should not have
• physical address

```html
<!DOCTYPE html>
<html lang="en">
<head>
<meta charset="utf-8">
<title>Vextorial — Business Card</title>
<link href="https://fonts.googleapis.com/css2?family=Open+Sans:wght@400;600;800&display=swap" rel="stylesheet">
<style>
  :root {
    --stage: #121212;
    --brand-blue: #3d74b9;
    --card-dark: #212125;
    --accent-orange: #ef7f22;
    --edge-orange: #b85c12;
    --text-light: #f4f4f4;
    --rule: #bfbfbf;
  }
  * { box-sizing: border-box; margin: 0; padding: 0; }
  html, body {
    width: 1200px; height: 936px; overflow: hidden;
    background: var(--stage);
    font-family: "Open Sans", sans-serif;
  }
  .stage {
    width: 1200px; height: 936px;
    display: flex; flex-direction: column; align-items: center; justify-content: center;
    gap: 56px;
  }
  .card {
    width: 600px; height: 343px;
    border-radius: 26px;
    border: 3px solid var(--accent-orange);
    box-shadow: 0 4px 0 var(--edge-orange), 0 14px 30px rgba(0,0,0,.6);
    position: relative;
    overflow: hidden;
  }
  /* front side */
  .card-front {
    background: var(--brand-blue);
    display: flex; flex-direction: column; align-items: center; justify-content: center;
    color: #fff;
  }
  .company-name {
    font-weight: 800; font-size: 72px; letter-spacing: 1px; line-height: 1;
  }
  .tagline {
    font-weight: 400; font-size: 27px; margin-top: 8px; letter-spacing: -.2px;
  }
  /* back side */
  .card-back {
    background: var(--card-dark);
    color: var(--text-light);
    display: flex; flex-direction: column; align-items: center;
    padding-top: 40px;
  }
  .brand-lockup { display: flex; align-items: center; gap: 12px; }
  .brand-square { width: 34px; height: 34px; background: var(--brand-blue); }
  .brand-name {
    font-weight: 800; font-size: 30px; color: var(--brand-blue); letter-spacing: 1px;
  }
  .person-name {
    font-weight: 800; font-size: 46px; margin-top: 24px; line-height: 1;
  }
  .person-name .first { color: var(--accent-orange); }
  .person-name .last { color: var(--brand-blue); }
  .contact-block { width: 530px; margin-top: 26px; }
  .rule { height: 1px; background: var(--rule); opacity: .8; }
  .contact-row {
    display: flex; justify-content: space-between; align-items: center;
    padding: 10px 4px; font-size: 15px;
  }
  .contact-item { display: flex; align-items: center; gap: 7px; white-space: nowrap; }
  .icon { width: 16px; height: 16px; fill: var(--accent-orange); }
  .services { text-align: center; padding: 10px 0; font-size: 15px; }
</style>
</head>
<body>
<main class="stage">
  <section class="card card-front" aria-label="Card front">
    <div class="company-name">VEXTORIAL</div>
    <div class="tagline">developer of custom applications</div>
  </section>

  <section class="card card-back" aria-label="Card back">
    <div class="brand-lockup">
      <span class="brand-square"></span>
      <span class="brand-name">VEXTORIAL</span>
    </div>
    <div class="person-name"><span class="first">Dale</span> <span class="last">Parker</span></div>
    <div class="contact-block">
      <div class="rule"></div>
      <div class="contact-row">
        <span class="contact-item">
          <svg class="icon" viewBox="0 0 24 24" aria-hidden="true"><path d="M6.6 10.8a15 15 0 0 0 6.6 6.6l2.2-2.2a1 1 0 0 1 1-.25 11.4 11.4 0 0 0 3.6.57 1 1 0 0 1 1 1V20a1 1 0 0 1-1 1A17 17 0 0 1 3 4a1 1 0 0 1 1-1h3.5a1 1 0 0 1 1 1c0 1.25.2 2.45.57 3.6a1 1 0 0 1-.25 1z"/></svg>
          (888) 555-VXTRL
        </span>
        <span class="contact-item">
          <svg class="icon" viewBox="0 0 24 24" aria-hidden="true"><path d="M2 5h20v14H2z M4 7v.5l8 5 8-5V7z" fill-rule="evenodd"/></svg>
          dale@vextorial.com
        </span>
        <span class="contact-item">
          <svg class="icon" viewBox="0 0 24 24" aria-hidden="true"><circle cx="12" cy="12" r="10"/><path d="M2 12h20M12 2c3 3 3 17 0 20M12 2c-3 3-3 17 0 20" stroke="#212125" stroke-width="1.4" fill="none"/></svg>
          www.vextorial.com
        </span>
      </div>
      <div class="rule"></div>
      <div class="services">Custom software · Bitcoin education &amp; payment integration</div>
      <div class="rule"></div>
    </div>
  </section>
</main>
</body>
</html>
```